Web Design For Manufacturing And Outsourcing Company

Pick up the pieces from our previous developer and help us complete our website.

5 pages - Home,Machining,Sourcing,About Us, and Contact

Attached you will find screen shots of previous direction but we're open to new ideas.

We can provide all text and images needed.

Thanks!

Number of Pages Required

5+ page

```html
<!DOCTYPE html>
<html lang="en">
<head>
<meta charset="utf-8">
<title>Kestrel Industries – Home</title>
<link href="https://fonts.googleapis.com/css2?family=Lato:wght@400;700;900&display=swap" rel="stylesheet">
<style>
:root{
  --orange:#e8541e;
  --ink:#2b2b2b;
  --text:#3a3a3a;
  --muted:#555;
  --panel:#efefef;
  --dark:#2a2a2a;
  --white:#ffffff;
}
*{margin:0;padding:0;box-sizing:border-box}
html,body{width:1200px;height:2586px;overflow:hidden;background:var(--white)}
body{font-family:'Lato',sans-serif;color:var(--text);position:relative}

.site-header{position:absolute;top:0;left:0;width:1200px;height:76px;background:var(--white);display:flex;align-items:center;justify-content:space-between;padding:0 73px 0 76px;box-shadow:0 1px 3px rgba(0,0,0,.08);z-index:2}
.brand{display:flex;align-items:center;gap:10px;font-weight:900;font-size:17px;letter-spacing:3px;color:var(--orange)}
.brand-mark{width:16px;height:22px;background:var(--ink)}
.main-nav{display:flex;gap:34px}
.main-nav a{font-size:14.5px;font-weight:700;color:var(--ink);text-decoration:none;text-transform:uppercase;letter-spacing:.2px}
.main-nav a.is-active{color:var(--orange)}

.hero{position:absolute;top:76px;left:0;width:1200px;height:558px;background:linear-gradient(120deg,#3a3d42 0%,#6b7076 40%,#8c9197 55%,#4b4f55 80%,#2e3034 100%);display:flex;align-items:center;justify-content:center}
.hero-title{font-size:48px;font-weight:900;color:var(--white);text-align:center;line-height:50px;margin-top:-6px}

.about{position:absolute;top:634px;left:0;width:1200px;height:487px;text-align:center}
.section-title{font-size:34px;font-weight:900;color:var(--ink);letter-spacing:.3px}
.about .section-title{position:absolute;top:56px;left:0;width:100%}
.eyebrow{font-size:19px;font-weight:900;color:var(--orange);text-transform:uppercase}
.quality-title{position:absolute;top:126px;left:0;width:100%}
.quality-text{position:absolute;top:155px;left:72px;width:1056px;font-size:14.5px;line-height:27.5px;color:var(--text)}
.values-title{position:absolute;top:275px;left:0;width:100%}
.values{position:absolute;top:325px;left:0;width:100%}
.value{position:absolute;width:340px;margin-left:-170px}
.value h3{font-size:15.5px;font-weight:900;color:#111;margin-bottom:8px}
.value p{font-size:14.5px;line-height:25px}

.feature{position:absolute;left:0;width:1200px;height:560px}
.solutions{top:1121px;background:var(--panel)}
.machining{top:1681px;background:var(--white)}
.photo{position:absolute;top:0;height:560px}
.solutions .photo{left:0;width:587px;background:linear-gradient(135deg,#dfe6ee 0%,#9aa7b5 35%,#5b6775 60%,#c3ccd6 100%)}
.machining .photo{left:612px;width:588px;background:radial-gradient(circle at 45% 40%,#f4b07a 0%,#b8683a 30%,#5a3424 65%,#2a1d18 100%)}
.feature-body{position:absolute;top:54px;width:520px}
.solutions .feature-body{left:615px}
.machining .feature-body{left:76px}
.feature-body .section-title{text-align:left}
.feature-intro{font-size:14.5px;line-height:25px;margin-top:18px;color:var(--text)}
.feature-list{list-style:none;margin-top:20px}
.feature-item{display:flex;align-items:flex-start;height:100px}
.feature-icon{width:64px;height:64px;flex:none;margin-right:33px}
.feature-item h4{font-size:19px;font-weight:900;color:var(--orange);line-height:22px;margin-top:2px}
.feature-item p{font-size:14.5px;line-height:25px;color:var(--text);margin-top:2px}

.cta{position:absolute;top:2241px;left:0;width:1200px;height:262px;background:var(--dark);text-align:center}
.cta-title{position:absolute;top:56px;left:0;width:100%;font-size:29px;font-weight:900;color:var(--white);line-height:36px;text-transform:uppercase}
.cta-button{position:absolute;top:152px;left:497px;width:206px;height:48px;border-radius:24px;background:var(--orange);color:var(--white);font-size:16.5px;font-weight:900;line-height:48px;text-decoration:none;text-transform:uppercase}

.site-footer{position:absolute;top:2503px;left:0;width:1200px;height:83px;text-align:center;line-height:83px;font-size:13.5px;color:var(--muted)}
</style>
</head>
<body>

<header class="site-header">
  <div class="brand"><span class="brand-mark"></span>KESTREL INDUSTRIES</div>
  <nav class="main-nav">
    <a href="#" class="is-active">Home</a>
    <a href="#">Machining Capablities</a>
    <a href="#">Sourcing</a>
    <a href="#">Contact Us</a>
  </nav>
</header>

<section class="hero" role="img" aria-label="Close-up of a CNC milling machine spraying coolant over a metal part">
  <h1 class="hero-title">A single point of contact for all your<br>procurement needs.</h1>
</section>

<section class="about">
  <h2 class="section-title">ABOUT US</h2>
  <h3 class="eyebrow quality-title">Quality Policy:</h3>
  <p class="quality-text">We are committed to consistently exceeding customer expectations by&nbsp; providing products, services and sourcing solutions of the highest standard of qual-<br>ity. With our streamlined processes our method is efficient, provides value and ensures on time delivery. Our success is based on continuously improving the<br>efficiencies and effectiveness of our products, processes, and quality management systems.</p>
  <h3 class="eyebrow values-title">Core Values:</h3>
  <div class="values">
    <div class="value" style="left:240px">
      <h3>TEAMWORK</h3>
      <p>We are one company, one team. We understand<br>when we work together we work smarter<br>and not harder.</p>
    </div>
    <div class="value" style="left:600px">
      <h3>RESPECT</h3>
      <p>We treat others as we expect to be t<br>reated, showing consideration for those<br>around us.</p>
    </div>
    <div class="value" style="left:958px">
      <h3>GRATITUDE</h3>
      <p>We appreciate where we have come from and<br>the opportunities we are given to<br>continue our journey.</p>
    </div>
  </div>
</section>

<section class="feature solutions">
  <div class="photo" role="img" aria-label="CNC lathe turning a steel shaft"></div>
  <div class="feature-body">
    <h2 class="section-title">SOLUTIONS</h2>
    <p class="feature-intro">Lorem ipsum dolor sit amet, consectetur adipiscing elit. Aenean quam arcu,<br>dictum at finibus ac, lobortis vel nisl. Donec ultrices aliquam diam, ac<br>vestibulum nisi rutrum eget.</p>
    <ul class="feature-list">
      <li class="feature-item">
        <svg class="feature-icon" viewBox="0 0 64 64" aria-hidden="true"><path d="M14 6h26l12 12v40H14z" fill="#f08a5d" stroke="#2b2b2b" stroke-width="2.5" stroke-linejoin="round"/><path d="M40 6v12h12" fill="none" stroke="#2b2b2b" stroke-width="2.5"/><path d="M22 28h22M22 36h22M22 44h22" stroke="#2b2b2b" stroke-width="2.5"/></svg>
        <div><h4>CONSECTETU</h4><p>Aenean quam arcu, dictum at finibus ac, lobortis vel nisl.<br>Donec ultrices aliquam diam, ac vestibulum..</p></div>
      </li>
      <li class="feature-item">
        <svg class="feature-icon" viewBox="0 0 64 64" aria-hidden="true"><g fill="#f08a5d" stroke="#2b2b2b" stroke-width="2.2"><circle cx="14" cy="20" r="6"/><circle cx="50" cy="20" r="6"/><path d="M3 44c0-9 5-14 11-14s11 5 11 14z"/><path d="M39 44c0-9 5-14 11-14s11 5 11 14z"/><circle cx="32" cy="24" r="8"/><path d="M17 56c0-12 7-18 15-18s15 6 15 18z"/></g></svg>
        <div><h4>CONSECTETU</h4><p>Aenean quam arcu, dictum at finibus ac, lobortis vel nisl.<br>Donec ultrices aliquam diam, ac vestibulum..</p></div>
      </li>
      <li class="feature-item">
        <svg class="feature-icon" viewBox="0 0 64 64" aria-hidden="true"><path d="M4 4v54h58" fill="none" stroke="#2b2b2b" stroke-width="2.5"/><g fill="#f08a5d" stroke="#2b2b2b" stroke-width="2"><rect x="12" y="38" width="8" height="16"/><rect x="24" y="30" width="8" height="24"/><rect x="36" y="34" width="8" height="20"/><rect x="48" y="20" width="8" height="34"/></g></svg>
        <div><h4>CONSECTETU</h4><p>Aenean quam arcu, dictum at finibus ac, lobortis vel nisl.<br>Donec ultrices aliquam diam, ac vestibulum..</p></div>
      </li>
    </ul>
  </div>
</section>

<section class="feature machining">
  <div class="feature-body">
    <h2 class="section-title">MACHINING</h2>
    <p class="feature-intro">Lorem ipsum dolor sit amet, consectetur adipiscing elit. Aenean quam arcu,<br>dictum at finibus ac, lobortis vel nisl. Donec ultrices aliquam diam, ac<br>vestibulum nisi rutrum eget.</p>
    <ul class="feature-list">
      <li class="feature-item">
        <svg class="feature-icon" viewBox="0 0 64 64" aria-hidden="true"><g fill="#f08a5d" stroke="#2b2b2b" stroke-width="2.2"><circle cx="24" cy="28" r="14" stroke-dasharray="5 3"/><circle cx="24" cy="28" r="5" fill="#fff"/><circle cx="46" cy="46" r="10" stroke-dasharray="4 2.5"/><circle cx="46" cy="46" r="3.5" fill="#fff"/></g></svg>
        <div><h4>CONSECTETU</h4><p>Aenean quam arcu, dictum at finibus ac, lobortis vel nisl.<br>Donec ultrices aliquam diam, ac vestibulum..</p></div>
      </li>
      <li class="feature-item">
        <svg class="feature-icon" viewBox="0 0 64 64" aria-hidden="true"><g fill="#f08a5d" stroke="#2b2b2b" stroke-width="2.2"><rect x="4" y="30" width="56" height="20"/><rect x="10" y="16" width="16" height="14"/><rect x="36" y="10" width="10" height="20"/><rect x="8" y="50" width="8" height="6"/><rect x="48" y="50" width="8" height="6"/></g><path d="M12 40h40" stroke="#2b2b2b" stroke-width="2"/></svg>
        <div><h4>CONSECTETU</h4><p>Aenean quam arcu, dictum at finibus ac, lobortis vel nisl.<br>Donec ultrices aliquam diam, ac vestibulum..</p></div>
      </li>
      <li class="feature-item">
        <svg class="feature-icon" viewBox="0 0 64 64" aria-hidden="true"><g stroke="#2b2b2b" stroke-width="2.2" fill="#f08a5d" stroke-linejoin="round"><path d="M10 54l26-26 6 6-26 26-6 0z"/><path d="M40 6a12 12 0 0 0 -6 18l6 6a12 12 0 0 0 18 -6l-8 2-6-6 2-8z"/><path d="M8 10l6-4 30 30-4 4z"/><path d="M42 40l14 14-4 4-14-14z"/></g></svg>
        <div><h4>CONSECTETU</h4><p>Aenean quam arcu, dictum at finibus ac, lobortis vel nisl.<br>Donec ultrices aliquam diam, ac vestibulum..</p></div>
      </li>
    </ul>
  </div>
  <div class="photo" role="img" aria-label="Grinding wheel on a metal shaft throwing orange sparks"></div>
</section>

<section class="cta">
  <h2 class="cta-title">Contact us today with your machining<br>or sourcing needs!</h2>
  <a href="#" class="cta-button">Get in touch</a>
</section>

<footer class="site-footer">Copyright © 2019 .Company Name All Right Reserved</footer>

</body>
</html>
```